Aunt Roula's Bakery

I am about to create a luxury boutique that specializes in cake baking and cupcake
and ready for parties and special events and order delivery
the logo has already made

Boutique

Email:auntroulasbakery@mailbox-example.net
Instagram: aunt_roula_bakery
Twitter: xxxxxxx
WhatsApp: xxxxxxx

Requirements
Must have
• luxury design

```html
<!DOCTYPE html>
<html lang="en">
<head>
<meta charset="utf-8">
<title>Aunt Roula's Bakery – Business Card</title>
<link rel="stylesheet" href="https://fonts.googleapis.com/css2?family=Open+Sans:wght@400;600&display=swap">
<style>
  :root {
    --page-bg: #e6e4e5;
    --card-white: #f8f8f8;
    --brand-pink: #d58b9e;
    --card-pink: #d4909f;
    --ink-grey: #5f5e5c;
    --text-grey: #4a4a4a;
    --band-grey: #737370;
    --rule-grey: #cfcfcf;
    --white: #ffffff;
  }
  * { margin: 0; padding: 0; box-sizing: border-box; }
  html, body {
    width: 1200px; height: 750px; overflow: hidden;
    background: var(--page-bg);
    font-family: "Open Sans", Arial, sans-serif;
  }
  .canvas { position: relative; width: 1200px; height: 750px; }

  .card {
    position: absolute; top: 228px;
    width: 461px; height: 263px;
    overflow: hidden;
  }
  .card--front { left: 124px; background: var(--card-white); }
  .card--back  { left: 618px; background: var(--card-pink); }

  /* brand lockup */
  .brand {
    position: absolute; text-align: center;
    display: flex; flex-direction: column; align-items: center;
  }
  .brand__disc { border-radius: 50%; }
  .brand__name { font-weight: 400; line-height: 1.1; margin-top: 10px; white-space: nowrap; }
  .brand__name span { display: block; }
  .brand__name .brand__sub { letter-spacing: 0.5em; margin-top: 4px; padding-left: 0.5em; }

  .card--front .brand { left: 26px; top: 60px; width: 170px; }
  .card--front .brand__disc {
    width: 42px; height: 42px; background: var(--brand-pink);
    border: 2px solid var(--ink-grey);
  }
  .card--front .brand__name { color: var(--ink-grey); font-size: 19px; }
  .card--front .brand__name .brand__sub { font-size: 12px; }

  .card--back .brand { left: 0; top: 54px; width: 100%; }
  .card--back .brand__disc { width: 60px; height: 60px; border: 3px solid var(--white); }
  .card--back .brand__name { color: var(--white); font-size: 27px; margin-top: 14px; }
  .card--back .brand__name .brand__sub { font-size: 15px; margin-top: 6px; }

  .divider {
    position: absolute; left: 206px; top: 56px;
    width: 1px; height: 128px; background: var(--rule-grey);
  }

  .contact { position: absolute; left: 222px; top: 52px; }
  .contact__name { color: var(--brand-pink); font-size: 17px; font-weight: 600; line-height: 1.3; white-space: nowrap; }
  .contact__role { color: var(--ink-grey); font-size: 12px; line-height: 1.3; margin-bottom: 9px; white-space: nowrap; }
  .contact__list { list-style: none; }
  .contact__item {
    display: flex; align-items: center; gap: 8px;
    color: var(--text-grey); font-size: 10.5px; line-height: 17.5px; height: 17.5px;
    white-space: nowrap;
  }
  .contact__item--email { letter-spacing: -0.15px; }
  .contact__icon { width: 12px; height: 12px; flex: none; }

  .web-band {
    position: absolute; left: 0; top: 231px; width: 100%; height: 19px;
    background: var(--band-grey);
  }
  .web-band__pink {
    position: absolute; left: 0; top: 0; width: 356px; height: 19px;
    background: var(--brand-pink);
  }
  .web-band__url {
    position: absolute; left: 87px; top: 0; line-height: 19px;
    color: var(--white); font-size: 10.5px; letter-spacing: 0.12em; white-space: nowrap;
  }
  .web-band__disc {
    position: absolute; left: 346px; top: -4px; width: 27px; height: 27px;
    border-radius: 50%; background: var(--brand-pink);
    border: 2px solid var(--white); box-shadow: 0 0 0 1px var(--band-grey);
  }
</style>
</head>
<body>
<main class="canvas">

  <section class="card card--front" aria-label="Business card front">
    <div class="brand">
      <div class="brand__disc"></div>
      <p class="brand__name"><span>Aunt Roula's</span><span class="brand__sub">BAKERY</span></p>
    </div>

    <div class="divider"></div>

    <div class="contact">
      <p class="contact__name">Mark Rivers</p>
      <p class="contact__role">CEO/Founder</p>
      <ul class="contact__list">
        <li class="contact__item">
          <svg class="contact__icon" viewBox="0 0 12 12" aria-hidden="true">
            <path d="M2.5 1 L4.5 1 L5.3 3.6 L4 4.6 C4.6 6 5.9 7.4 7.4 8 L8.4 6.7 L11 7.5 L11 9.5 C11 10.4 10.3 11 9.5 11 C5 10.6 1.4 7 1 2.5 C1 1.7 1.6 1 2.5 1 Z" fill="var(--brand-pink)"/>
          </svg>555 014 2290</li>
        <li class="contact__item contact__item--email">
          <svg class="contact__icon" viewBox="0 0 12 12" aria-hidden="true">
            <rect x="0.5" y="2.5" width="11" height="7.5" fill="var(--brand-pink)"/>
            <path d="M0.5 2.5 L6 6.8 L11.5 2.5" fill="none" stroke="var(--white)" stroke-width="1"/>
          </svg>auntroulasbakery@mailbox-example.net</li>
        <li class="contact__item">
          <svg class="contact__icon" viewBox="0 0 12 12" aria-hidden="true"><circle cx="6" cy="6" r="5" fill="var(--brand-pink)"/></svg>aunt_roula_bakery</li>
        <li class="contact__item">
          <svg class="contact__icon" viewBox="0 0 12 12" aria-hidden="true"><circle cx="6" cy="6" r="5" fill="var(--brand-pink)"/></svg>auntroulasbakery</li>
        <li class="contact__item">
          <svg class="contact__icon" viewBox="0 0 12 12" aria-hidden="true"><circle cx="6" cy="6" r="5" fill="var(--brand-pink)"/></svg>auntroulasbakery</li>
      </ul>
    </div>

    <div class="web-band">
      <div class="web-band__pink"></div>
      <p class="web-band__url">www.auntroulasbakery.example</p>
      <div class="web-band__disc"></div>
    </div>
  </section>

  <section class="card card--back" aria-label="Business card back">
    <div class="brand">
      <div class="brand__disc"></div>
      <p class="brand__name"><span>Aunt Roula's</span><span class="brand__sub">BAKERY</span></p>
    </div>
  </section>

</main>
</body>
</html>
```